Website redesign for KestrelFinanceMan/TKFinanceMan

Job Title: Talented Web Designer for SEO-Friendly Website Creation & HostFalcon cPanel Integration
 
Inspiration: dunewheelracingexample.com
Pages:

About
Get a Quote
FAQ
Boat Loans
RV Loans
Testimonials
News/Blog
Affiliate Program
Contact

Job Description:
 
We are seeking a skilled and creative freelance web designer to build a stunning, SEO-optimized website for our business. The ideal candidate will have a strong design portfolio, technical expertise in creating search engine-friendly websites, and experience implementing websites into HostFalcon cPanel.
 
Project Overview:
 
Objective: Create a modern, motorsports themed visually appealing website that is optimized for SEO.

Platform: The site will be hosted on HostFalcon, so familiarity with their cPanel for setup and integration is essential.

Deliverables:
         •A fully functional website (desktop and mobile) with user-friendly navigation and a responsive design.
         •SEO best practices implemented throughout, including proper meta tags, optimized images, fast loading speeds, and mobile compatibility.
         •Seamless integration into HostFalcon cPanel for hosting.
         •Guidance or documentation on maintaining the site post-launch.
 
Key Skills Required:
 
         •Proficiency in web design (HTML, CSS, JavaScript, or relevant platforms like WordPress).
         •Knowledge of SEO principles and tools for website optimization.
         •Experience with HostFalcon cPanel, including file management and DNS settings.
         •Strong communication skills to understand our vision and provide progress updates.
 
What We’re Looking For:
 
         •A designer who can transform our ideas into a sleek and functional website.
         •Someone proactive in suggesting creative design elements and SEO improvements.
         •A reliable professional who can meet deadlines and deliver a polished product.
 
Please provide:
 
         1.A brief introduction and why you’re a good fit for this project.
         2.Examples of previous web design projects, especially those with SEO implementation.
         3.Your estimated timeline and cost for this project.
 
We are excited to work with a talented designer who can bring our vision to life. If you are passionate about web design and SEO, we’d love to hear from you!

Target Market(s)

Boat and RV buyers looking for a loan

Coding

Coded - Design and coding required

Number of Pages Required

5+ page

Colors
F0912C
F2A743
F7CA91
FBE8D2
FDF5EE

Requirements
Must have
• motorsports type design
Nice to have
• fcontact forms easy to use layout on brand and color scheme of kestrelfinanceman and tkfinanceman.example

```html
<!DOCTYPE html>
<html lang="en">
<head>
<meta charset="utf-8">
<title>KestrelFinanceMan – Boat Loans Made Easy</title>
<link href="https://fonts.googleapis.com/css2?family=Russo+One&family=Montserrat:wght@400;500;600;700&family=Lato:wght@400;700&display=swap" rel="stylesheet">
<style>
:root{
  --blue:#1f5f99;
  --blue-dark:#184d7e;
  --orange:#f0912c;
  --orange-2:#f2a743;
  --peach:#f7ca91;
  --cream:#fbe8d2;
  --ink:#111;
  --grey:#555;
  --field:#ececec;
}
*{box-sizing:border-box;margin:0;padding:0}
html,body{width:1200px;height:3978px;overflow:hidden;background:#fff;font-family:"Lato",sans-serif;color:var(--ink)}
.page{position:relative;width:1200px;height:3978px;overflow:hidden}
.abs{position:absolute}
.display{font-family:"Russo One",sans-serif;text-transform:uppercase}
.orange{color:var(--orange)}
.btn{position:absolute;display:flex;align-items:center;justify-content:center;font-family:"Montserrat",sans-serif;font-weight:700;font-size:16px;color:#fff;text-transform:uppercase;border-radius:3px}
.btn-blue{background:var(--blue)}
.btn-orange{background:var(--orange)}

/* top bar */
.topbar{top:0;left:0;width:1200px;height:40px;background:var(--blue);color:#fff;font:600 13px "Montserrat",sans-serif}
.topbar .item{position:absolute;top:0;height:40px;display:flex;align-items:center;gap:14px}
.topbar .sep{position:absolute;top:8px;width:1px;height:24px;background:#fff}

/* header */
.header{top:40px;left:0;width:1200px;height:105px;background:#fff}
.brand{position:absolute;left:106px;top:34px;font:700 26px "Montserrat",sans-serif;color:var(--orange);display:flex;align-items:center;gap:10px}
.brand .dot{width:22px;height:22px;border-radius:50%;background:var(--blue)}
.reviews{position:absolute;left:504px;top:22px;font:500 14px "Montserrat",sans-serif}
.stars{color:var(--orange);letter-spacing:1px}
.search{position:absolute;left:763px;top:33px;width:324px;height:42px;border-radius:4px;background:#eee;font:13px "Montserrat",sans-serif;color:#888;display:flex;align-items:center;padding:0 24px;justify-content:space-between}

/* nav */
.nav{top:145px;left:0;width:1200px;height:53px;background:var(--orange)}
.nav ul{list-style:none;position:absolute;left:103px;top:0;height:53px;display:flex;align-items:center;gap:6px}
.nav li{font:600 15px "Montserrat",sans-serif;color:#fff;padding:6px 10px;border-radius:3px}
.nav li.active{background:var(--blue)}
.nav .apply{position:absolute;left:959px;top:0;width:128px;height:53px;background:var(--blue);color:#fff;font:700 15px "Montserrat",sans-serif;display:flex;align-items:center;justify-content:center}

/* hero */
.hero{top:198px;left:0;width:1200px;height:594px;border-radius:0 0 0 90px;overflow:hidden;background:linear-gradient(180deg,#4e7fb3 0%,#7ea6cd 38%,#4d6c55 44%,#33628f 52%,#2b5b88 100%)}
.hero-corner{top:650px;left:1110px;width:90px;height:142px;background:var(--blue);border-radius:0 0 0 0}
.hero h1{position:absolute;left:111px;top:98px;font:400 54px "Russo One",sans-serif;color:#fff}
.hero p{position:absolute;left:111px;top:176px;font:15px "Lato",sans-serif;color:#fff}

/* calculator */
.calc{top:700px;left:111px;width:976px;height:180px;background:#fff;border-radius:40px;box-shadow:0 6px 14px rgba(0,0,0,.18)}
.calc label{position:absolute;top:42px;font:15px "Lato",sans-serif}
.calc .field{position:absolute;top:74px;width:218px;height:60px;background:var(--field);border-radius:3px}

/* boat types */
.eyebrow{font:700 15px "Montserrat",sans-serif;color:var(--blue);text-transform:uppercase}
.h2{font:400 44px "Russo One",sans-serif;text-transform:uppercase}
.card{top:1095px;width:309px;height:355px;background:#fff;box-shadow:0 2px 10px rgba(0,0,0,.15);border-radius:4px}
.card .img{position:absolute;left:10px;top:12px;width:289px;height:265px}
.card .name{position:absolute;left:20px;top:294px;font:400 21px "Lato",sans-serif}
.card .badge{position:absolute;right:24px;top:260px;width:86px;height:86px;border-radius:50%;background:#fff;display:flex;align-items:center;justify-content:center}
.arrow-circ{width:22px;height:22px;border-radius:50%;display:flex;align-items:center;justify-content:center}

/* about */
.about-img{top:1609px;left:0;width:641px;height:578px;background:linear-gradient(135deg,#5c6a70,#d9dcde 45%,#3f6e7e 70%,#2a5a6a);}
.about{top:1609px;left:648px;width:552px;height:578px;background:var(--blue);color:#fff}
.about ul{list-style:none;position:absolute;left:26px;top:270px}
.about li{display:flex;align-items:center;gap:20px;font:15px "Lato",sans-serif;height:33.5px}

/* finance more */
.svc{position:absolute;top:2310px;width:160px;text-align:center;font:700 13px "Montserrat",sans-serif}
.svc .ic{width:86px;height:86px;border-radius:50%;margin:0 auto 22px;display:flex;align-items:center;justify-content:center}

/* reviews */
.rev-bg{top:2599px;left:0;width:1200px;height:569px;background:linear-gradient(180deg,#fbfcfd 0%,#e4ecf3 45%,#7d8f96 62%,#2e6ea1 80%,#1e5c90 100%)}
.review{top:2805px;width:473px;height:258px;background:#fff;box-shadow:0 2px 10px rgba(0,0,0,.15)}
.review .av{position:absolute;left:20px;top:22px;width:64px;height:64px;border-radius:50%}
.review .who{position:absolute;left:96px;top:32px;font:500 16px "Montserrat",sans-serif}
.review .st{position:absolute;left:96px;top:56px;font-size:14px}
.review .q{position:absolute;right:24px;top:28px;font:400 48px "Russo One",sans-serif;color:#ccc;line-height:1}
.review p{position:absolute;left:28px;top:112px;width:420px;font:13px/22px "Lato",sans-serif;color:#333}
.review .more{position:absolute;left:28px;top:218px;font:13px Georgia,serif;color:#555;text-decoration:underline}

/* partners */
.partner{top:3283px;width:100px;height:66px;border-radius:8px;background:#dfe4ea}

/* footer */
.footer{top:3493px;left:0;width:1200px;height:485px;background:#000;border-radius:90px 90px 0 0}
.cta{top:3420px;left:142px;width:974px;height:212px;background:#fff;border-radius:30px;border-top:6px solid var(--orange);box-shadow:0 4px 10px rgba(0,0,0,.2)}
.cta .col{position:absolute;top:50px;width:240px;text-align:center;font:500 21px "Lato",sans-serif}
.cta .ic{width:74px;height:74px;border-radius:50%;margin:0 auto 16px;display:flex;align-items:center;justify-content:center}
.cta .div{position:absolute;top:28px;height:164px;border-left:2px dashed var(--blue)}
.foot h4{font:500 21px "Lato",sans-serif;color:var(--orange);margin-bottom:14px}
.foot li{list-style:none;font:11px "Lato",sans-serif;color:#fff;line-height:22.5px}
.contact-row{display:flex;gap:16px;color:#fff;font:11px/20px "Lato",sans-serif;margin-bottom:18px}
.copy{top:3952px;left:0;width:1200px;text-align:center;color:#fff;font:13px "Lato",sans-serif}
</style>
</head>
<body>
<div class="page">

<!-- top bar -->
<div class="abs topbar">
  <div class="item" style="left:114px">
    <svg width="18" height="18" viewBox="0 0 24 24"><path fill="#fff" d="M6.6 10.8a15 15 0 0 0 6.6 6.6l2.2-2.2c.3-.3.7-.4 1-.2 1.1.4 2.3.6 3.6.6.6 0 1 .4 1 1V20c0 .6-.4 1-1 1A17 17 0 0 1 3 4c0-.6.4-1 1-1h3.5c.6 0 1 .4 1 1 0 1.3.2 2.5.6 3.6.1.3 0 .7-.2 1z"/></svg>
    619-555-0142
  </div>
  <div class="sep" style="left:299px"></div>
  <div class="item" style="left:339px">
    <svg width="20" height="20" viewBox="0 0 24 24"><rect x="1" y="1" width="22" height="22" rx="3" fill="#fff"/><path fill="#1f5f99" d="M12 4a6 6 0 0 0-6 6c0 4.5 6 10 6 10s6-5.5 6-10a6 6 0 0 0-6-6zm0 8.2a2.2 2.2 0 1 1 0-4.4 2.2 2.2 0 0 1 0 4.4z"/></svg>
    4180 Harbor Reach Way Ste. 210, Bayview, CA 90000
  </div>
  <div class="sep" style="left:840px"></div>
  <div class="item" style="left:886px">
    <svg width="20" height="20" viewBox="0 0 24 24"><rect x="1" y="1" width="22" height="22" rx="3" fill="#fff"/><rect x="5" y="7" width="14" height="10" fill="none" stroke="#1f5f99" stroke-width="1.8"/><path d="M5 7l7 6 7-6" fill="none" stroke="#1f5f99" stroke-width="1.8"/></svg>
    Dana@kestrelfinanceman.com
  </div>
</div>

<!-- header -->
<div class="abs header">
  <div class="brand"><span class="dot"></span>KestrelFinanceMan</div>
  <div class="reviews">
    <div><b style="color:var(--blue)">T</b> <span class="stars">★★★★★</span> (1606)</div>
    <div style="margin-top:10px">Based On Trustpoint reviews</div>
  </div>
  <div class="search">Search Here
    <svg width="16" height="16" viewBox="0 0 24 24"><circle cx="10" cy="10" r="7" fill="none" stroke="#333" stroke-width="2.4"/><path d="M15 15l6 6" stroke="#333" stroke-width="2.4"/></svg>
  </div>
</div>

<!-- nav -->
<nav class="abs nav">
  <ul>
    <li>Home</li><li>About</li><li>Get a Quote</li><li>FAQ</li><li class="active">Boat Loans</li><li>RV Loans</li><li>Blog</li><li>Affiliate Program</li><li>Contact</li>
  </ul>
  <div class="apply">APPLY NOW</div>
</nav>

<!-- hero -->
<div class="abs hero-corner"></div>
<section class="abs hero" role="img" aria-label="Photo of a white pontoon boat with red outboard engines speeding across a lake">
  <h1>Boat Loans Made Easy!</h1>
  <p>Welcome to KestrelFinanceMan.com, your one-stop resource for all of your boat financing</p>
  <div class="btn btn-orange" style="left:111px;top:232px;width:150px;height:44px">Get Started</div>
</section>

<!-- calculator -->
<div class="abs calc">
  <label style="left:32px">Loan Amount</label>
  <label style="left:276px">Rate (APR)</label>
  <label style="left:521px">Team(Years)</label>
  <div class="field" style="left:23px"></div>
  <div class="field" style="left:267px"></div>
  <div class="field" style="left:512px"></div>
  <div class="btn btn-blue" style="left:742px;top:74px;width:218px;height:60px;font-size:14px">Calulate Payments</div>
</div>

<!-- boat types -->
<div class="abs eyebrow" style="top:970px;left:0;width:1206px;text-align:center">Apply Now</div>
<h2 class="abs h2" style="top:1002px;left:0;width:1200px;text-align:center">We Finance <span class="orange">All Types of Boats!</span></h2>

<div class="abs arrow-circ" style="left:37px;top:1247px;background:var(--orange)"><svg width="12" height="12" viewBox="0 0 12 12"><path d="M2 6h7M6 3l3 3-3 3" stroke="#fff" stroke-width="1.8" fill="none"/></svg></div>
<div class="abs arrow-circ" style="left:1126px;top:1247px;background:#bbb"><svg width="12" height="12" viewBox="0 0 12 12"><path d="M2 6h7M6 3l3 3-3 3" stroke="#fff" stroke-width="1.8" fill="none"/></svg></div>

<div class="abs card" style="left:113px">
  <div class="img" role="img" aria-label="Photo of a pontoon boat at a marina" style="background:linear-gradient(180deg,#5a8fcf 0%,#b79b74 30%,#2c9c96 60%,#1a7e84 100%)"></div>
  <div class="badge"><svg width="64" height="26" viewBox="0 0 64 26"><path d="M4 16h56l-6 8H10z" fill="#1f5f99"/><path d="M22 8h22l4 8H20z" fill="#1f5f99"/></svg></div>
  <div class="name">Pontoons</div>
</div>
<div class="abs card" style="left:445px">
  <div class="img" role="img" aria-label="Photo of a yellow performance boat on open water" style="background:linear-gradient(180deg,#9cc4e6 0%,#4f8dbf 45%,#c9b23a 62%,#2f6d9c 80%,#2a6896 100%)"></div>
  <div class="badge"><svg width="74" height="26" viewBox="0 0 74 26"><path d="M2 14h70l-8 9H12z" fill="#f0912c"/><path d="M24 6h26l6 8H20z" fill="#f0912c"/></svg></div>
  <div class="name orange">Center Consoles</div>
</div>
<div class="abs card" style="left:777px">
  <div class="img" role="img" aria-label="Photo of a tow boat cruising on a lake" style="background:linear-gradient(180deg,#6a9cc9 0%,#7b8e5c 25%,#4f86ae 45%,#9dbfd8 70%,#3f79a6 100%);height:259px"></div>
  <div class="badge"><svg width="66" height="28" viewBox="0 0 66 28"><path d="M2 16h62l-7 9H10z" fill="#1f5f99"/><path d="M16 6h32v3H16zM22 9h20l4 7H18z" fill="#1f5f99"/></svg></div>
  <div class="name">Tow Boats</div>
</div>
<div class="btn btn-blue" style="left:525px;top:1476px;width:150px;height:45px">Apply Now</div>

<!-- about -->
<div class="abs about-img" role="img" aria-label="Aerial photo of boats tied together with people swimming in the water"></div>
<svg class="abs" style="left:560px;top:1609px" width="100" height="578" viewBox="0 0 100 578"><path d="M88 578V110C88 60 60 20 0 0h100v578z" fill="var(--blue)"/><path d="M82 578V110C82 62 56 22 4 0" fill="none" stroke="#fff" stroke-width="6"/></svg>
<section class="abs about">
  <div class="eyebrow" style="position:absolute;left:24px;top:56px;color:#fff">About Us</div>
  <h2 style="position:absolute;left:24px;top:84px;font:400 33px/42px 'Russo One',sans-serif;text-transform:uppercase">Your Trusted Source<br>for Marine Financing.</h2>
  <p style="position:absolute;left:26px;top:180px;width:430px;font:13px/26px 'Lato',sans-serif">Our goal is to make your boat purchase as quick and stress-free as possible. Our numerous lender relationships Allow us to offer competitive rates and terms with quick turn-around times.</p>
  <ul>
    <li><svg width="18" height="18" viewBox="0 0 18 18"><circle cx="9" cy="9" r="9" fill="#fff"/><path d="M5 9h7M9 6l3 3-3 3" stroke="#1f5f99" stroke-width="1.8" fill="none"/></svg>Loans from $25,000 - $5M</li>
    <li><svg width="18" height="18" viewBox="0 0 18 18"><circle cx="9" cy="9" r="9" fill="#fff"/><path d="M5 9h7M9 6l3 3-3 3" stroke="#1f5f99" stroke-width="1.8" fill="none"/></svg>Up to 25yrs old</li>
    <li><svg width="18" height="18" viewBox="0 0 18 18"><circle cx="9" cy="9" r="9" fill="#fff"/><path d="M5 9h7M9 6l3 3-3 3" stroke="#1f5f99" stroke-width="1.8" fill="none"/></svg>Same-Day Approvals</li>
    <li><svg width="18" height="18" viewBox="0 0 18 18"><circle cx="9" cy="9" r="9" fill="#fff"/><path d="M5 9h7M9 6l3 3-3 3" stroke="#1f5f99" stroke-width="1.8" fill="none"/></svg>Quick Funding</li>
    <li><svg width="18" height="18" viewBox="0 0 18 18"><circle cx="9" cy="9" r="9" fill="#fff"/><path d="M5 9h7M9 6l3 3-3 3" stroke="#1f5f99" stroke-width="1.8" fill="none"/></svg>Private Party or Dealer</li>
    <li><svg width="18" height="18" viewBox="0 0 18 18"><circle cx="9" cy="9" r="9" fill="#fff"/><path d="M5 9h7M9 6l3 3-3 3" stroke="#1f5f99" stroke-width="1.8" fill="none"/></svg>Best Rates in the Industry</li>
  </ul>
  <div class="btn btn-orange" style="left:28px;top:487px;width:151px;height:46px">Read More</div>
</section>

<!-- finance more -->
<div class="abs eyebrow" style="left:111px;top:2271px">Finance</div>
<h2 class="abs" style="left:110px;top:2299px;font:400 44px/54px 'Russo One',sans-serif;text-transform:uppercase">We Finance More<br><span class="orange">Than Just Boats</span></h2>
<p class="abs" style="left:115px;top:2413px;width:440px;font:13px/26px 'Lato',sans-serif;color:var(--grey)">At Harbor Crest Recreational Finance, we are your one-stop resource for all marine, RV and Airplane Financing</p>
<div class="btn btn-blue" style="left:111px;top:2470px;width:152px;height:45px">Contact Us</div>

<div class="svc" style="left:576px">
  <div class="ic" style="background:var(--blue)"><svg width="46" height="46" viewBox="0 0 46 46"><path d="M22 6v26H8zM25 10l13 22H25z" fill="#fff"/><path d="M6 35h34l-4 5H10z" fill="#fff"/></svg></div>Marine Financing</div>
<div class="svc" style="left:768px;color:var(--blue)">
  <div class="ic" style="background:var(--orange)"><svg width="48" height="40" viewBox="0 0 48 40"><rect x="4" y="6" width="40" height="24" rx="3" fill="none" stroke="#fff" stroke-width="3"/><rect x="10" y="12" width="8" height="7" fill="#fff"/><rect x="22" y="12" width="8" height="7" fill="#fff"/><rect x="34" y="12" width="6" height="14" fill="#fff"/><circle cx="14" cy="33" r="4" fill="#fff"/><circle cx="34" cy="33" r="4" fill="#fff"/><rect x="14" y="1" width="20" height="4" fill="#fff"/></svg></div>RV Financing</div>
<div class="svc" style="left:955px">
  <div class="ic" style="background:var(--blue)"><svg width="44" height="44" viewBox="0 0 24 24"><path fill="#fff" d="M21 16v-2l-8-5V3.5a1.5 1.5 0 0 0-3 0V9l-8 5v2l8-2.5V19l-2 1.5V22l3.5-1 3.5 1v-1.5L13 19v-5.5z" transform="rotate(90 12 12)"/></svg></div>Aircraft Financing</div>

<!-- reviews -->
<section class="abs rev-bg" role="img" aria-label="Background photo of a boat speeding through spray near desert hills"></section>
<div class="abs eyebrow" style="top:2688px;left:0;width:1208px;text-align:center">Reviews</div>
<h2 class="abs h2" style="top:2718px;left:0;width:1070px;text-align:center">What Our <span class="orange">Customers Say?</span></h2>
<div class="abs arrow-circ" style="left:43px;top:2922px;background:var(--blue)"><svg width="12" height="12" viewBox="0 0 12 12"><path d="M2 6h7M6 3l3 3-3 3" stroke="#fff" stroke-width="1.8" fill="none"/></svg></div>
<div class="abs arrow-circ" style="left:1121px;top:2922px;background:#3b4f66"><svg width="12" height="12" viewBox="0 0 12 12"><path d="M2 6h7M6 3l3 3-3 3" stroke="#fff" stroke-width="1.8" fill="none"/></svg></div>

<div class="abs review" style="left:111px">
  <div class="av" role="img" aria-label="Reviewer portrait" style="background:#b7a48f"></div>
  <div class="who">Corey</div>
  <div class="st"><b style="color:var(--blue)">T</b> <span class="stars">★★★★★</span></div>
  <div class="q">”</div>
  <p>I have nothing but outstanding things to say about Lena. From my initial phone call in March, I knew that I was in good hands. Always there to answer all my questions either through text or a phone call.</p>
  <div class="more">Read More….</div>
</div>
<div class="abs review" style="left:600px">
  <div class="av" role="img" aria-label="Reviewer portrait" style="background:#c79b7d"></div>
  <div class="who">Tessa Ruiz</div>
  <div class="st"><b style="color:var(--blue)">T</b> <span class="stars">★★★★★</span></div>
  <div class="q">”</div>
  <p style="top:96px">Just purchased a boat and used Harbor Crest and they made the process very easy. Lena Marsh helped every step of the way and was always available when I had any questions. She was quick to keep me updated and streamlined the entire process of paperwork and funding.</p>
  <div class="more">Read More….</div>
</div>

<!-- partners -->
<div class="abs partner" style="left:125px" role="img" aria-label="Partner badge"></div>
<div class="abs partner" style="left:290px;border-radius:50%;width:72px;height:72px;top:3280px;left:302px" role="img" aria-label="Partner badge"></div>
<div class="abs partner" style="left:452px" role="img" aria-label="Partner badge"></div>
<div class="abs partner" style="left:614px" role="img" aria-label="Partner badge"></div>
<div class="abs partner" style="left:774px;height:46px;top:3293px" role="img" aria-label="Partner badge"></div>
<div class="abs partner" style="left:938px;width:130px;height:36px;top:3298px" role="img" aria-label="Partner badge"></div>

<!-- footer -->
<footer class="abs footer"></footer>
<div class="abs cta">
  <div class="col" style="left:10px"><div class="ic" style="background:var(--orange)"><svg width="30" height="30" viewBox="0 0 24 24"><path fill="#fff" d="M6.6 10.8a15 15 0 0 0 6.6 6.6l2.2-2.2c.3-.3.7-.4 1-.2 1.1.4 2.3.6 3.6.6.6 0 1 .4 1 1V20c0 .6-.4 1-1 1A17 17 0 0 1 3 4c0-.6.4-1 1-1h3.5c.6 0 1 .4 1 1 0 1.3.2 2.5.6 3.6.1.3 0 .7-.2 1z"/></svg></div>Call Us</div>
  <div class="div" style="left:214px"></div>
  <div class="col" style="left:245px"><div class="ic" style="background:var(--blue)"><svg width="32" height="32" viewBox="0 0 32 32"><circle cx="16" cy="16" r="13" fill="none" stroke="#fff" stroke-width="2.2"/><rect x="9" y="11" width="14" height="10" fill="none" stroke="#fff" stroke-width="2"/><path d="M9 11l7 6 7-6" fill="none" stroke="#fff" stroke-width="2"/></svg></div>Email Us</div>
  <div class="div" style="left:462px"></div>
  <div class="col" style="left:488px"><div class="ic" style="background:var(--orange)"><svg width="32" height="32" viewBox="0 0 32 32"><rect x="5" y="4" width="18" height="8" rx="2" fill="none" stroke="#fff" stroke-width="2"/><path d="M14 14v10l-3-3M14 24l6-2 4 2v6H12z" fill="none" stroke="#fff" stroke-width="2"/></svg></div>Apply</div>
  <div class="div" style="left:710px"></div>
  <div class="col" style="left:731px"><div class="ic" style="background:var(--blue)"><svg width="32" height="32" viewBox="0 0 32 32"><path d="M6 18v8h20v-8" fill="#fff"/><path d="M16 4v14M10 10l6-6 6 6" fill="none" stroke="#fff" stroke-width="2.4"/></svg></div>Upload Docs</div>
</div>

<div class="abs foot" style="left:103px;top:3706px;width:350px">
  <div style="font:700 26px 'Montserrat',sans-serif;color:var(--orange);display:flex;align-items:center;gap:10px"><span style="width:22px;height:22px;border-radius:50%;background:var(--blue);display:inline-block"></span>KestrelFinanceMan</div>
  <p style="margin-top:32px;font:12px/27px 'Lato',sans-serif;color:#fff;width:350px">Welcome to Harbor Crest Recreational Finance, your one-stop resource for all of your financing needs for the Marine &amp; RV Industries throughout the US.</p>
</div>

<div class="abs foot" style="left:527px;top:3678px">
  <h4>Quick Links</h4>
  <ul><li>About</li><li>Get a Quote</li><li>FAQ</li><li>Boat Loans</li><li>RV Loans</li><li>Testimonials</li><li>News/Blog</li><li>Affiliate Program</li><li>Contact</li></ul>
</div>
<div class="abs foot" style="left:709px;top:3678px">
  <h4>Services</h4>
  <ul><li>Boats Financing</li><li>RV's Financing</li><li>Aircraft Financing</li></ul>
  <h4 style="margin-top:14px">Follow Us</h4>
  <ul>
    <li style="display:flex;align-items:center;gap:12px;margin-bottom:6px"><span style="width:18px;height:18px;background:#fff;display:inline-block"></span>Faceplate</li>
    <li style="display:flex;align-items:center;gap:12px;margin-bottom:6px"><span style="width:18px;height:18px;background:#fff;display:inline-block"></span>Chirper</li>
    <li style="display:flex;align-items:center;gap:12px"><span style="width:18px;height:18px;background:#fff;display:inline-block"></span>Snapgram</li>
  </ul>
</div>
<div class="abs foot" style="left:880px;top:3678px;width:220px">
  <h4>Contact Info</h4>
  <div class="contact-row"><svg width="22" height="22" viewBox="0 0 24 24"><rect x="1" y="1" width="22" height="22" rx="3" fill="#fff"/><path fill="#000" d="M12 4a6 6 0 0 0-6 6c0 4.5 6 10 6 10s6-5.5 6-10a6 6 0 0 0-6-6zm0 8.2a2.2 2.2 0 1 1 0-4.4 2.2 2.2 0 0 1 0 4.4z"/></svg><span>4180 Harbor Reach Way Ste.<br>210, Bayview, CA 90000</span></div>
  <div class="contact-row"><svg width="22" height="22" viewBox="0 0 24 24"><rect x="1" y="1" width="22" height="22" rx="3" fill="#fff"/><path fill="#000" d="M8 11a9 9 0 0 0 5 5l1.5-1.5 3 1.3V19c-7 0-13-6-13-13h3.2l1.3 3z"/></svg><span style="padding-top:6px">(619) 555-0142</span></div>
  <div class="contact-row"><svg width="22" height="22" viewBox="0 0 24 24"><rect x="1" y="1" width="22" height="22" rx="3" fill="#fff"/><rect x="5" y="7" width="14" height="10" fill="none" stroke="#000" stroke-width="1.8"/><path d="M5 7l7 6 7-6" fill="none" stroke="#000" stroke-width="1.8"/></svg><span style="padding-top:4px">Dana@kestrelfinanceman.com</span></div>
</div>

<div class="abs" style="left:111px;top:3933px;width:976px;height:1px;background:#666"></div>
<div class="abs copy">© 2024 Kestrelfinanceman.com. All rights reserved.</div>

</div>
</body>
</html>
```